Redesign website for small print company

Vindurgata is a small printing company in Iceland mainly servicing Students, schools, etc. We are also doing all kind of other jobs, like business cards, book printing, brochure printing etc. We are also selling books online.
Our website is: www.vindurgata.is
What we are looking for is:
- Web Design (Uncoded - PSD layout only)
- Mobile friendly design, using our current color scheme: Red, green, yellow and light gray.
- Clean simple design
- Simple, light and easy to use.
- More menu Items/drop down
Industry/Entity Type
Digital Printing
Number of Pages Required
5+ page
Requirements
Must have
- Easy navigation
- Designed for mobile
- Current color scheme (see logo)
Nice to have
- Icon based products

```html
<!DOCTYPE html>
<html lang="en">
<head>
<meta charset="utf-8">
<title>Vindurgata – Printing for Schools and Everyone</title>
<link href="https://fonts.googleapis.com/css2?family=Lato:wght@400;700;900&display=swap" rel="stylesheet">
<style>
:root{
  --red:#e8312f;
  --green:#0b6b33;
  --yellow:#f5c400;
  --gray:#f3f3f3;
  --card:#f0f0f0;
  --ink:#1d1d1d;
  --muted:#555;
  --dark:#2e2e2e;
  --social:#5a5a5a;
}
*{box-sizing:border-box;margin:0;padding:0}
html,body{width:1200px;height:3930px;overflow:hidden}
body{font-family:'Lato',Arial,sans-serif;color:var(--ink);background:#fff;position:relative}
.abs{position:absolute}
.stripe{height:5px;display:flex}
.stripe span{flex:1}
.s-r{background:var(--red)}.s-y{background:var(--yellow)}.s-g{background:var(--green)}
/* header */
.site-header{position:absolute;left:0;width:1200px;background:#fff}
.brand{position:absolute;left:112px;top:17px;display:flex;align-items:center;gap:10px}
.brand-square{width:40px;height:40px;background:var(--red)}
.brand-name{font-weight:900;font-size:34px;letter-spacing:.5px;color:var(--ink)}
.util{position:absolute;top:18px;left:745px;display:flex;align-items:center;gap:26px;font-size:15px;font-weight:700}
.util div{display:flex;align-items:center;gap:8px}
.main-nav{position:absolute;top:62px;left:645px;display:flex;gap:58px;font-size:14px;font-weight:700}
.main-nav a{color:var(--ink);text-decoration:none;padding-bottom:8px}
.main-nav a.active{color:var(--red);border-bottom:2px solid var(--red)}
/* hero */
.hero{position:absolute;top:95px;left:0;width:1200px;height:500px;
  background:radial-gradient(ellipse at 15% 30%,#f6d24a 0,transparent 45%),radial-gradient(ellipse at 85% 35%,#b8d85a 0,transparent 45%),radial-gradient(ellipse at 50% 40%,#d8e6ef 0,transparent 50%),linear-gradient(#eaf0e6,#fbfbf7)}
.hero-products{position:absolute;left:250px;top:40px;width:660px;height:340px;border-radius:6px;
  background:linear-gradient(120deg,#e4e4e4,#c9c9c9 40%,#8a6b4f 60%,#e9e2d6)}
.hero-title{position:absolute;top:390px;width:1200px;text-align:center;color:var(--red);font-weight:700;font-size:24px;line-height:33px}
.hero-notch{position:absolute;left:592px;top:595px;width:0;height:0;border-left:10px solid transparent;border-right:10px solid transparent;border-top:10px solid var(--red)}
/* section headings */
.sec-title{position:absolute;width:1200px;text-align:center;font-weight:900;font-size:27px;letter-spacing:.5px}
.tri-line{position:absolute;left:540px;width:120px;height:4px;display:flex}
.tri-line span{flex:1}
/* welcome */
.welcome{position:absolute;top:595px;left:0;width:1200px;height:475px;background:var(--gray)}
.welcome h2{position:absolute;left:115px;top:72px;font-size:28px;font-weight:900}
.welcome h2 .thin{font-weight:700}
.welcome .lead{position:absolute;left:115px;top:140px;width:680px;font-size:14px;font-weight:700;line-height:22px}
.welcome .body{position:absolute;left:115px;width:680px;font-size:13px;color:var(--muted);line-height:22px}
.btn-read{position:absolute;left:115px;top:355px;background:#111;color:#fff;font-size:13px;font-weight:700;padding:8px 14px}
.welcome-photo{position:absolute;left:820px;top:80px;width:160px;height:300px;
  background:linear-gradient(#2a2a2a,#6a6a6a 45%,#c9c9c9 60%,#e8c04a 80%,#7fb27f)}
/* products */
.card{position:absolute;width:300px;height:205px;background:var(--card);text-align:center}
.card.active{background:#fff;box-shadow:0 2px 10px rgba(0,0,0,.2)}
.card .ring{position:absolute;left:118px;top:38px;width:64px;height:64px;border:3px solid var(--yellow);border-radius:50%;background:#fff;display:flex;align-items:center;justify-content:center}
.card .label{position:absolute;top:132px;width:100%;font-weight:900;font-size:17px}
/* help */
.help{position:absolute;top:1720px;left:0;width:1200px;height:425px;background:var(--gray)}
.help-box{position:absolute;top:163px;width:420px;height:152px;color:#fff;padding:26px 20px 0 146px}
.help-box h3{font-size:19px;font-weight:700;margin-bottom:6px}
.help-box p{font-size:12.5px;line-height:18px}
.help-box .big{font-size:22px;font-weight:900;margin-top:10px}
.help-box .mail{font-size:17px;font-weight:700;margin-top:6px}
.help-icon{position:absolute;left:40px;top:40px;width:72px;height:72px;border-radius:50%;background:#fff;display:flex;align-items:center;justify-content:center}
/* get started */
.step{position:absolute;top:2290px;width:165px;height:165px;background:var(--card);text-align:center}
.step .disc{position:absolute;left:37px;top:-40px;width:90px;height:90px;border-radius:50%;background:#fff;box-shadow:0 0 0 1px #e3e3e3;display:flex;align-items:center;justify-content:center}
.step .txt{position:absolute;top:94px;width:100%;font-size:20px;line-height:26px;color:#333;white-space:nowrap}
.step .txt b{font-weight:700}
/* testimonial */
.testi{position:absolute;top:2520px;left:0;width:1200px;height:450px;background:var(--gray)}
.avatar{position:absolute;left:200px;top:150px;width:135px;height:135px;border-radius:50%;border:4px solid var(--red);background:radial-gradient(circle at 50% 40%,#e8d3c2,#c9b39c 60%,#f2f2f2)}
.quote{position:absolute;left:365px;top:155px;width:680px;font-size:14px;font-style:italic;line-height:25px;color:#444}
.quote .q{color:var(--red);font-size:28px;font-weight:900;font-style:normal;line-height:0}
.quote-author{position:absolute;left:790px;top:285px;width:250px;text-align:right;font-size:13px;font-style:italic;font-weight:700;color:#333}
.stars{position:absolute;left:955px;top:302px;color:var(--green);font-size:15px;letter-spacing:1px}
.dots{position:absolute;left:533px;top:360px;display:flex;gap:6px}
.dots span{width:7px;height:7px;border-radius:50%;background:#ccc}
.dots span:first-child{background:var(--red)}
/* printlife */
.printlife-art{position:absolute;left:505px;top:3125px;width:200px;height:255px;background:linear-gradient(#fbe89a,#f8d4b0 50%,#f6b3ad)}
.feature{position:absolute;display:flex;align-items:center;gap:14px;font-size:21px;line-height:26px;color:#222}
.rule{position:absolute;height:2px}
.rule::before,.rule::after{content:"";position:absolute;top:-5px;width:10px;height:10px;border-radius:50%;border:2px solid currentColor;background:#fff}
.rule::before{left:-6px}.rule::after{right:-6px}
/* footer */
.site-footer{position:absolute;top:3475px;left:0;width:1200px;height:335px;background:var(--dark);color:#ddd}
.foot-menu{position:absolute;top:38px;left:0;width:1200px;display:flex;justify-content:space-around;padding:0 100px;font-size:17px;color:#eee}
.foot-menu span::after{content:" ⌄";color:#aaa}
.foot-divider{position:absolute;top:80px;left:0;width:1200px;height:1px;background:#444}
.fcol{position:absolute;top:120px;font-size:16px;color:#eee}
.fcol small{font-size:13px;color:#ccc}
.social{display:flex;gap:8px;margin-top:14px}
.social span{width:22px;height:22px;border-radius:50%;background:var(--social)}
.news{display:flex;margin-top:18px}
.news .field{width:255px;height:30px;background:#fff;color:#555;font-size:11px;padding:9px 8px}
.news .send{width:65px;height:30px;background:var(--red)}
.pay{display:flex;gap:6px;align-items:center;margin-top:14px;font-size:12px;color:#ccc}
.pay span{width:32px;height:18px;background:#f1f1f1;border-radius:2px}
.contact p{display:flex;gap:10px;margin-top:12px;font-size:13px;line-height:17px}
.copyright{position:absolute;top:308px;width:1200px;text-align:center;font-size:11px;color:#bbb}
.offline{position:absolute;right:0;top:298px;width:240px;height:30px;background:var(--red);color:#fff;font-size:12px;font-weight:700;padding:8px 18px}
.perks{position:absolute;top:3810px;left:0;width:1200px;height:120px;background:var(--green);color:#fff}
.perk{position:absolute;top:28px;display:flex;align-items:center;gap:16px;font-size:18px;line-height:24px}
.perk .badge{width:60px;height:60px;border-radius:50%;background:var(--yellow)}
</style>
</head>
<body>

<div class="abs" style="top:0;left:0;width:1200px"><div class="stripe"><span class="s-r"></span><span class="s-y"></span><span class="s-g"></span></div></div>

<header class="site-header" style="top:5px;height:90px">
  <div class="brand"><span class="brand-square"></span><span class="brand-name">VINDURGATA</span></div>
  <div class="util">
    <div><svg width="20" height="20" viewBox="0 0 24 24"><path d="M6.6 10.8a15 15 0 006.6 6.6l2.2-2.2c.3-.3.7-.4 1-.2 1.1.4 2.3.6 3.6.6.6 0 1 .4 1 1V20c0 .6-.4 1-1 1A17 17 0 013 4c0-.6.4-1 1-1h3.5c.6 0 1 .4 1 1 0 1.3.2 2.5.6 3.6.1.3 0 .7-.2 1z" fill="#333"/></svg>5550142</div>
    <div><svg width="20" height="20" viewBox="0 0 24 24"><circle cx="12" cy="12" r="9" fill="none" stroke="#333" stroke-width="2"/><path d="M12 7v5l3 2" stroke="#333" stroke-width="2" fill="none"/></svg>Mon - Fri: 9-17</div>
    <div style="margin-left:40px"><svg width="22" height="22" viewBox="0 0 24 24"><circle cx="10" cy="10" r="7" fill="none" stroke="#333" stroke-width="2"/><path d="M15 15l6 6" stroke="#333" stroke-width="2"/></svg></div>
    <div><svg width="24" height="22" viewBox="0 0 24 22"><path d="M1 2h4l3 12h12l3-9H7" fill="none" stroke="#333" stroke-width="2"/><circle cx="10" cy="19" r="2" fill="#333"/><circle cx="18" cy="19" r="2" fill="#333"/></svg></div>
  </div>
  <nav class="main-nav"><a class="active">HOME</a><a>SERVICES</a><a>JOB SUBMIT</a><a>ABOUT US</a></nav>
</header>

<section class="hero">
  <div class="hero-products" role="img" aria-label="Stacks of printed business cards, flyers and a wedding brochure on a watercolour background"></div>
  <h1 class="hero-title">Vindurgata Is Specialized In The Service of School Staff,<br>As Well As Providing General Public Printing</h1>
</section>
<div class="hero-notch"></div>

<section class="welcome">
  <h2><span class="thin">WELCOME TO</span>&nbsp; VINDURGATA</h2>
  <div class="tri-line" style="left:115px;top:116px;width:95px"><span class="s-r"></span><span class="s-y"></span><span class="s-g"></span></div>
  <p class="lead">University education is a company located in the campus, which has specialized in the service of school staff, as well as providing general public printing.</p>
  <p class="body" style="top:200px">Higher education publishes seminars and first-class textbooks for courses, prints theses for lesson, as well as working on an unprecedented number of smaller pieces for students, teachers and organizations. These include brochures, reports, questionnaires, business cards, books, OCR scanning and more.</p>
  <p class="body" style="top:290px">Higher education is a tailored print shop. The Green Leaf is the official eco-label of the Nordic countries, which has created a foothold in this country and is known among consumers.</p>
  <div class="btn-read">Read More</div>
  <div class="welcome-photo" role="img" aria-label="Photo of a printed door hanger and a colour swatch fan"></div>
</section>

<h2 class="sec-title" style="top:1123px">OUR PRODUCTS</h2>
<div class="tri-line" style="top:1165px"><span class="s-r"></span><span class="s-y"></span><span class="s-g"></span></div>

<div class="card active" style="left:113px;top:1208px"><div class="ring"><svg width="30" height="34" viewBox="0 0 30 34"><rect x="4" y="2" width="22" height="30" fill="none" stroke="var(--red)" stroke-width="2.5"/><path d="M9 10h12M9 16h12M9 22h8" stroke="var(--red)" stroke-width="2.5"/></svg></div><div class="label">ESSAYS</div></div>
<div class="card" style="left:450px;top:1208px"><div class="ring"><svg width="34" height="26" viewBox="0 0 34 26"><rect x="2" y="2" width="30" height="22" rx="2" fill="none" stroke="var(--red)" stroke-width="2.5"/><circle cx="11" cy="11" r="4" fill="var(--red)"/><path d="M19 9h9M19 15h9" stroke="var(--red)" stroke-width="2.5"/></svg></div><div class="label">BUSINESS CARDS</div></div>
<div class="card" style="left:788px;top:1208px"><div class="ring"><svg width="34" height="30" viewBox="0 0 34 30"><path d="M2 4l10-2 10 2 10-2v24l-10 2-10-2-10 2z" fill="none" stroke="var(--red)" stroke-width="2.5"/><path d="M12 2v24M22 4v24" stroke="var(--red)" stroke-width="2"/></svg></div><div class="label">LEAFLETS</div></div>
<div class="card" style="left:113px;top:1450px"><div class="ring"><svg width="30" height="34" viewBox="0 0 30 34"><rect x="5" y="2" width="20" height="30" rx="2" fill="none" stroke="var(--red)" stroke-width="2.5"/><rect x="10" y="8" width="10" height="8" fill="var(--red)"/><path d="M9 22h12M9 27h12" stroke="var(--red)" stroke-width="2.5"/></svg></div><div class="label">BOOK PRINTING</div></div>
<div class="card" style="left:450px;top:1450px"><div class="ring"><svg width="28" height="34" viewBox="0 0 28 34"><rect x="3" y="2" width="22" height="30" fill="none" stroke="var(--red)" stroke-width="2.5"/><path d="M7 22l6-8 4 5 3-3 4 6z" fill="var(--red)"/></svg></div><div class="label">POSTERS</div></div>
<div class="card" style="left:788px;top:1450px"><div class="ring"><svg width="30" height="34" viewBox="0 0 30 34"><path d="M5 4h18v28H5z" fill="none" stroke="var(--red)" stroke-width="2.5"/><path d="M9 4v28" stroke="var(--red)" stroke-width="2"/><path d="M13 12h7M13 18h7" stroke="var(--red)" stroke-width="2.5"/></svg></div><div class="label">TEXTBOOKS</div></div>

<section class="help">
  <h2 class="sec-title" style="top:58px">WE ARE HERE TO HELP YOU</h2>
  <div class="tri-line" style="top:100px"><span class="s-r"></span><span class="s-y"></span><span class="s-g"></span></div>
  <div class="help-box" style="left:172px;background:var(--red)">
    <div class="help-icon"><svg width="40" height="40" viewBox="0 0 40 40"><circle cx="20" cy="15" r="8" fill="var(--red)"/><path d="M6 38c0-9 6-14 14-14s14 5 14 14z" fill="var(--red)"/><path d="M9 16a11 11 0 0122 0" fill="none" stroke="var(--red)" stroke-width="3"/></svg></div>
    <h3>Get Real-time Design Help</h3>
    <p>Start from scratch, customize a template, or<br>upload your own logo or complete design.</p>
    <div class="big">5550142</div>
  </div>
  <div class="help-box" style="left:620px;background:var(--green)">
    <div class="help-icon"><svg width="42" height="30" viewBox="0 0 42 30"><path d="M2 8l8-4 10 4 6-3 14 6-6 8-8 6-10-6-8 0-6-6z" fill="var(--green)"/></svg></div>
    <h3>For Bulk Order</h3>
    <p>Need support on your special or bulk<br>orders? Just mail us at</p>
    <div class="mail">verk@vindurgata.is</div>
  </div>
</section>

<h2 class="sec-title" style="top:2195px">GET STARTED</h2>
<div class="tri-line" style="top:2237px"><span class="s-r"></span><span class="s-y"></span><span class="s-g"></span></div>

<div class="step" style="left:162px"><div class="disc"><svg width="44" height="44" viewBox="0 0 44 44"><path d="M22 4l12 14h-7v12H17V18h-7z" fill="var(--yellow)"/><path d="M6 30v10h32V30" fill="none" stroke="var(--yellow)" stroke-width="4"/></svg></div><div class="txt"><b style="color:var(--yellow)">U</b>pload<br>Your design</div></div>
<div class="step" style="left:393px"><div class="disc"><svg width="48" height="44" viewBox="0 0 48 44"><rect x="4" y="6" width="34" height="28" fill="none" stroke="var(--green)" stroke-width="3"/><rect x="12" y="12" width="34" height="28" fill="#fff" stroke="#333" stroke-width="3"/><path d="M18 20h22M18 27h14" stroke="var(--green)" stroke-width="3"/></svg></div><div class="txt"><b style="color:var(--green)">U</b>se Our<br>Free Templates</div></div>
<div class="step" style="left:618px"><div class="disc"><svg width="46" height="44" viewBox="0 0 46 44"><rect x="3" y="4" width="40" height="28" fill="none" stroke="var(--red)" stroke-width="3"/><path d="M16 40h14M23 32v8" stroke="#333" stroke-width="3"/><path d="M12 24l14-14 4 4-14 14h-4z" fill="var(--red)"/></svg></div><div class="txt"><b style="color:var(--red)">C</b>ustom Your<br>Design</div></div>
<div class="step" style="left:846px"><div class="disc"><svg width="44" height="44" viewBox="0 0 44 44"><rect x="4" y="4" width="36" height="36" fill="#222"/><path d="M10 12h24M10 20h12M10 28h12M26 20h8v8h-8z" stroke="#fff" stroke-width="3" fill="none"/></svg></div><div class="txt"><b>B</b>ulk<br>Enquiry</div></div>

<section class="testi">
  <h2 class="sec-title" style="top:72px">WHAT PEOPLE SAY ABOUT US?</h2>
  <div class="tri-line" style="top:114px"><span class="s-r"></span><span class="s-y"></span><span class="s-g"></span></div>
  <div class="avatar" role="img" aria-label="Portrait photo of a customer"></div>
  <p class="quote"><span class="q">“</span> Lorem ipsum dolor sit amet, consectetur adipiscing elit, sed do eiusmod tempor incididunt ut labore et dolore magna aliqua. Ut enim veniam, quis nostrud exercitation ullamco laboris nisi ut aliquip ex ea commodo consequat. Duis aute irure dolor in reprehenderit in voluptate velit esse cillum dolore eu fugiat nulla pariatur. Excepteur sint occaecat cupidatat non proident, sunt in culpa qui officia . <span class="q">”</span></p>
  <div class="quote-author">- Sconsectetur adipiscing</div>
  <div class="stars">★★★★★</div>
  <div class="dots"><span></span><span></span><span></span></div>
</section>

<h2 class="sec-title" style="top:3022px">WE MAKE YOUR PRINTLIFE BETTER</h2>
<div class="tri-line" style="top:3064px"><span class="s-r"></span><span class="s-y"></span><span class="s-g"></span></div>

<div class="rule" style="left:172px;top:3127px;width:310px;background:var(--yellow);color:var(--yellow)"></div>
<div class="rule" style="left:722px;top:3127px;width:310px;background:var(--green);color:var(--green)"></div>
<div class="rule" style="left:172px;top:3385px;width:310px;background:var(--red);color:var(--red)"></div>
<div class="rule" style="left:722px;top:3385px;width:310px;background:#222;color:#222"></div>

<div class="printlife-art" role="img" aria-label="Illustration of a printed door hanger in pastel yellow and pink"></div>

<div class="feature" style="left:168px;top:3148px"><svg width="40" height="38" viewBox="0 0 40 38"><rect x="1" y="4" width="32" height="22" rx="2" fill="#222"/><rect x="1" y="9" width="32" height="4" fill="#fff"/><rect x="22" y="20" width="16" height="14" rx="2" fill="var(--red)"/><path d="M25 20v-4a5 5 0 0110 0v4" fill="none" stroke="var(--red)" stroke-width="2"/></svg><span>Secured<br>Payment</span></div>
<div class="feature" style="left:835px;top:3148px;text-align:right"><span>Eco Friendly<br>Materials</span><svg width="60" height="60" viewBox="0 0 60 60"><circle cx="30" cy="30" r="24" fill="none" stroke="var(--yellow)" stroke-width="6"/><path d="M20 40c0-14 10-22 22-22-2 14-10 22-22 22z" fill="var(--green)"/></svg></div>
<div class="feature" style="left:168px;top:3305px"><svg width="44" height="44" viewBox="0 0 44 44"><path d="M6 38l4-12 22-22 8 8-22 22z" fill="var(--green)" stroke="#222" stroke-width="2"/><path d="M4 30l10 10" stroke="var(--red)" stroke-width="4"/></svg><span>Creating Designs<br>Of Your Own</span></div>
<div class="feature" style="left:805px;top:3305px;text-align:right"><span>Home Delivery<br>Options</span><svg width="64" height="44" viewBox="0 0 64 44"><rect x="2" y="6" width="38" height="26" fill="var(--red)"/><path d="M40 14h12l8 10v8H40z" fill="#222"/><circle cx="14" cy="36" r="5" fill="#222"/><circle cx="50" cy="36" r="5" fill="#222"/></svg></div>

<footer class="site-footer">
  <div class="abs" style="top:0;left:0;width:1200px"><div class="stripe"><span class="s-r"></span><span class="s-y"></span><span class="s-g"></span><span class="s-r"></span><span class="s-y"></span><span class="s-g"></span><span class="s-r"></span><span class="s-y"></span><span class="s-g"></span></div></div>
  <div class="foot-menu"><span>Let Us Help</span><span>What We Offer</span><span>Our Company</span><span>Our Policies</span></div>
  <div class="foot-divider"></div>
  <div class="fcol" style="left:115px">Connect With Us
    <div class="social"><span></span><span></span><span></span><span></span></div>
    <div style="display:flex;align-items:center;gap:8px;margin-top:30px"><span style="width:20px;height:20px;background:#eee"></span><span style="font-weight:900;font-size:18px">VINDURGATA</span></div>
  </div>
  <div class="fcol" style="left:375px">Sign Up For Newsletter
    <div class="news"><div class="field">Enter Your Email Here</div><div class="send"></div></div>
    <div class="pay"><small>We Accept</small><span></span><span></span><span></span><span></span><span></span></div>
  </div>
  <div class="fcol contact" style="left:818px">Contact Details
    <p><span style="color:var(--red)">●</span><span><b>VINDURGATA</b><br>Hlíðarvegur 14, 105 Reykjavík, Vsk: 480213</span></p>
    <p><span style="color:var(--red)">✆</span><span>5550142</span></p>
    <p><span style="color:var(--red)">✉</span><span>verk@vindurgata.is</span></p>
  </div>
  <div class="copyright">Copyright © 2018 Vindurgata . All Rights Reserved.</div>
  <div class="offline">Offline - Leave A Message</div>
</footer>

<section class="perks">
  <div class="perk" style="left:140px"><span class="badge"></span><span>Fast Turnaround<br>Within Days</span></div>
  <div class="perk" style="left:505px"><span class="badge"></span><span>Nationwide<br>Delivery</span></div>
  <div class="perk" style="left:825px"><span class="badge"></span><span>100% Quality<br>Products Guaranteed</span></div>
</section>

</body>
</html>
```